Floor Inspections and Consulting

We provide inspections and consulting services on various floor coverings, e.g. carpet, hardwood, etc. We also do expert witness work for attorneys due to floor covering failures. We current have a logo, just need it incorporated into a new design. I have examples of cards I have found on the internet that capture my attention and make a statement. I have included our original business card, which in my opinion is terrible, but it does have our logo on it.

```html
<!DOCTYPE html>
<html lang="en">
<head>
<meta charset="utf-8">
<title>Keystone Floor Reviews – Business Card</title>
<link href="https://fonts.googleapis.com/css2?family=Montserrat:wght@600&family=Open+Sans:wght@300;400&display=swap" rel="stylesheet">
<style>
  :root {
    --backdrop: #c8c8c8;
    --paper: #f0f0ef;
    --gold: #bea463;
    --charcoal: #2d2d2f;
    --charcoal-glow: #3a3834;
    --ink: #5a5a5a;
    --white: #ffffff;
  }
  * { margin: 0; padding: 0; box-sizing: border-box; }
  html, body { width: 1200px; height: 1200px; overflow: hidden; background: var(--backdrop); }
  .canvas { position: relative; width: 1200px; height: 1200px; }
  .card { position: absolute; left: 232px; width: 736px; height: 423px; border-radius: 38px; overflow: hidden; }

  .card-front { top: 106px; background: var(--paper); font-family: "Open Sans", sans-serif; font-weight: 300; color: var(--ink); }
  .name-band { position: absolute; left: 0; top: 88px; width: 518px; height: 76px; background: var(--gold); padding: 18px 0 0 70px; }
  .name { font-family: "Montserrat", sans-serif; font-weight: 600; font-size: 21px; color: var(--white); letter-spacing: 0.5px; line-height: 1.1; }
  .title { font-size: 16px; color: var(--white); line-height: 1.4; }

  .brand { position: absolute; right: 72px; top: 104px; display: flex; align-items: center; gap: 10px; }
  .brand-dot { width: 16px; height: 16px; border-radius: 50%; background: var(--gold); flex: none; }
  .brand-name { font-family: "Montserrat", sans-serif; font-weight: 600; font-size: 15px; line-height: 1.35; color: var(--gold); text-align: right; letter-spacing: 0.5px; }

  .address { position: absolute; left: 70px; top: 244px; font-size: 17px; line-height: 22px; }
  .contacts { position: absolute; left: 70px; top: 304px; list-style: none; font-size: 17px; line-height: 22px; }
  .contacts li { display: flex; align-items: center; gap: 9px; }
  .contacts svg { width: 14px; height: 14px; flex: none; }

  .tagline { position: absolute; right: 71px; top: 310px; text-align: right; font-size: 17px; line-height: 22px; }
  .tagline-rule { display: inline-block; width: 37px; height: 3px; background: var(--gold); margin-bottom: 17px; }
  .tagline-accent { color: var(--gold); }

  .card-back { top: 662px; background: var(--charcoal); }
  .back-texture { position: absolute; inset: 0; background: radial-gradient(circle at 50% 50%, var(--charcoal-glow) 0%, var(--charcoal) 70%); }
  .back-mark { position: absolute; left: 272px; top: 72px; width: 192px; height: 192px; border-radius: 50%; background: var(--gold); }
  .back-brand { position: absolute; left: 0; right: 0; top: 296px; text-align: center; font-family: "Montserrat", sans-serif; font-weight: 600; font-size: 20px; letter-spacing: 2px; color: var(--gold); }
</style>
</head>
<body>
<main class="canvas">

  <section class="card card-front">
    <div class="name-band">
      <p class="name">DANIEL MARROW</p>
      <p class="title">President</p>
    </div>

    <div class="brand">
      <span class="brand-dot"></span>
      <p class="brand-name">KEYSTONE<br>FLOOR REVIEWS</p>
    </div>

    <div class="address">
      <p>Keystone Floor Reviews</p>
      <p>P.O. Box 4417, Millbrook, CO 80999</p>
    </div>

    <ul class="contacts">
      <li>
        <svg viewBox="0 0 14 14" aria-hidden="true"><path d="M3 1.5l2.2 2.6-1.3 1.6c.8 1.8 2.2 3.2 4 4l1.6-1.3L12.5 11l-1.6 1.8C6 12.5 1.5 8 1.2 3.1z" fill="var(--gold)"/></svg>
        <span>555-014-2280</span>
      </li>
      <li>
        <svg viewBox="0 0 14 14" aria-hidden="true"><rect x="1" y="3" width="12" height="8.5" fill="var(--gold)"/><path d="M1 3l6 5 6-5" stroke="var(--paper)" stroke-width="1.2" fill="none"/></svg>
        <span>daniel@keystonefloor.com</span>
      </li>
      <li>
        <svg viewBox="0 0 14 14" aria-hidden="true"><circle cx="7" cy="7" r="6" fill="var(--gold)"/><path d="M1 7h12M7 1v12M7 1c-3 3-3 9 0 12M7 1c3 3 3 9 0 12" stroke="var(--paper)" stroke-width="0.8" fill="none"/></svg>
        <span>www.keystonefloor.com</span>
      </li>
    </ul>

    <div class="tagline">
      <span class="tagline-rule"></span>
      <p class="tagline-accent">Certified Floor Covering</p>
      <p>Inspections &amp; Consulting</p>
    </div>
  </section>

  <section class="card card-back">
    <div class="back-texture" role="img" aria-label="Faint gold concentric ring pattern radiating from the card centre"></div>
    <span class="back-mark"></span>
    <p class="back-brand">KEYSTONE FLOOR REVIEWS</p>
  </section>

</main>
</body>
</html>
```